Website to design and sell sundials: www.gnomonvale.com

We have a website that creates a free paper sundial, we want to migrate from this not profit free website to a website where we will continue offering the free paper sundial model but We will also offer a manufactured sundial and sell it.
In order to understand the project, please visit:
http://www.gnomonvale.com/vertical/sundial.html and
http://www.torvel.net/landing/

The website user journey should be redesigned, including the phases that are,
select language
Show product give info
Creation/edit sundial (could be one or more phases)
View created sundial
Buy sundial.

May some of them could be combined or splitted, what It have more sense.

Requirements
Must have
• A description page user journey offering freemium paper sundial and physical sundial to sell.
• A sundial creation page for "free" paper sundial
• A result page for paper sundial
• A sell page for physical

```html
<!DOCTYPE html>
<html lang="en">
<head>
<meta charset="utf-8">
<title>Gnomonvale – Sundials</title>
<link href="https://fonts.googleapis.com/css2?family=Dosis:wght@500;600;700&family=Open+Sans:wght@400;600&display=swap" rel="stylesheet">
<style>
:root{
  --red:#c0150f;
  --red-dark:#a20f0a;
  --ink:#333;
  --muted:#666;
  --line:#d9d9d9;
  --footer:#333;
  --footer-deep:#262626;
  --white:#fff;
}
*{box-sizing:border-box;margin:0;padding:0}
html,body{width:674px;height:1200px;overflow:hidden;background:var(--white)}
body{position:relative;font-family:"Open Sans",Arial,sans-serif;color:var(--ink)}
.abs{position:absolute}
.heading{font-family:"Dosis",Arial,sans-serif;font-weight:600;color:var(--red)}

/* header */
.top-rule{left:0;top:0;width:674px;height:2px;background:var(--red)}
.brand{left:74px;top:24px;display:flex;align-items:center;gap:7px;font-family:"Dosis",sans-serif;font-weight:600;font-size:21px;color:var(--red)}
.brand-dot{width:14px;height:14px;border-radius:50%;background:var(--red)}
.lang{left:554px;top:17px;width:45px;height:21px;border:1px solid #ccc;border-radius:3px;box-shadow:0 1px 2px rgba(0,0,0,.15);font-size:6px;display:flex;align-items:center;justify-content:center;gap:3px;color:#444}
.lang-flag{width:8px;height:8px;border-radius:50%;background:#2b3d8f;border:1px solid #c33}
.nav{top:58px;font-size:6.5px;letter-spacing:.5px;color:#444;transform:translateX(-50%)}
.nav.active{color:var(--red)}
.nav-bar{left:346px;top:78px;width:28px;height:2px;background:var(--red)}

/* hero */
.hero{left:0;top:80px;width:674px;height:249px;background:linear-gradient(90deg,#4b5a2a 0%,#6c7a3c 16%,#b8bcc4 32%,#d4d6dc 55%,#c9ccd2 75%,#5d6b31 85%,#3f4a22 100%)}
.hero-band{left:0;top:282px;width:674px;height:47px;background:rgba(40,40,40,.62)}
.hero-title{left:74px;top:292px;font-family:"Dosis",sans-serif;font-weight:700;font-size:21px;color:var(--white)}
.dot{top:302px;width:6px;height:6px;border-radius:50%;background:#ccc}
.dot.on{background:var(--red)}

/* welcome */
.welcome-art{left:74px;top:368px;width:138px;height:134px;background:linear-gradient(135deg,#f6f6f6,#ececec);border:1px solid #e0a0a0}
.welcome-title{left:243px;top:358px;font-size:17px}
.welcome-copy{left:243px;top:390px;width:356px;font-size:6.2px;line-height:10.8px;color:#555;text-align:justify}
.welcome-copy p+p{margin-top:10.8px}
.btn{background:var(--red);color:var(--white);border-radius:2px;display:flex;align-items:center;justify-content:center;box-shadow:0 1px 2px rgba(0,0,0,.25)}
.btn-more{left:243px;top:492px;width:62px;height:25px;font-size:6.2px}

/* creation */
.rule{left:0;width:674px;height:1px;background:var(--line)}
.creation{left:0;top:553px;width:674px;height:199px;background:linear-gradient(#fff,#efefef)}
.section-title{left:74px;font-size:17px}
.step{top:624px;width:100px;transform:translateX(-50%);text-align:center}
.step svg{width:22px;height:24px;display:block;margin:0 auto}
.step-name{margin-top:19px;font-family:"Dosis",sans-serif;font-weight:600;font-size:11px;color:var(--red);letter-spacing:.3px}
.step-text{margin-top:7px;font-size:6.8px;line-height:11px;color:#666}

/* gallery */
.arrows{left:584px;top:783px;font-size:11px;color:#222;letter-spacing:4px}
.card{top:817px;width:119px}
.card-photo{width:119px;height:79px;border:2px solid #fff;box-shadow:0 0 2px rgba(0,0,0,.35)}
.card-title{margin-top:15px;font-family:"Dosis",sans-serif;font-weight:500;font-size:11.5px;color:var(--red)}
.card-text{margin-top:2px;font-size:5.8px;line-height:11px;color:#555}
.btn-buy{margin-top:6px;width:48px;height:18px;font-size:5.6px}

/* footer */
.footer-rule{left:0;top:1009px;width:674px;height:3px;background:var(--red)}
.footer{left:0;top:1012px;width:674px;height:153px;background:var(--footer);color:#ddd}
.footer-bottom{left:0;top:1165px;width:674px;height:35px;background:var(--footer-deep);color:#ccc;font-size:5.8px;display:flex;align-items:center;justify-content:center}
.f-title{top:1033px;font-family:"Dosis",sans-serif;font-weight:600;font-size:11.5px;color:#f2f2f2}
.f-links{left:76px;top:1058px;font-size:5.6px;line-height:10.9px;color:#ddd;list-style:none}
.f-contact{left:186px;top:1060px;font-size:5.6px;color:#ddd;list-style:none}
.f-contact li{display:flex;gap:6px;align-items:flex-start;height:15px}
.f-contact li:last-child{line-height:7.5px}
.f-contact svg{width:7px;height:7px;flex:none;fill:#ddd}
.f-contact u{color:#eee}
.f-note{left:331px;top:1061px;font-size:5.4px;color:#ccc}
.f-input{left:331px;top:1079px;width:110px;height:19px;background:#5a5a5a;border:1px solid #6a6a6a;font-size:5.4px;color:#ddd;padding-left:6px;display:flex;align-items:center}
.f-btn{left:331px;top:1106px;width:47px;height:15px;font-size:5.6px;border-radius:0}
.f-brand{left:468px;top:1034px;display:flex;align-items:center;gap:5px;font-family:"Dosis",sans-serif;font-weight:600;font-size:12.5px;color:#b8b8b8}
.f-brand .brand-dot{width:10px;height:10px;background:#b8b8b8}
.social{top:1070px;width:18px;height:18px;border:1px solid #eee;border-radius:50%}
</style>
</head>
<body>

<div class="abs top-rule"></div>
<header>
  <div class="abs brand"><span class="brand-dot"></span>Gnomonvale.com</div>
  <div class="abs lang"><span class="lang-flag"></span>ENG
    <svg width="5" height="4" viewBox="0 0 5 4"><path d="M.5 1 2.5 3 4.5 1" stroke="#444" fill="none" stroke-width=".8"/></svg>
  </div>
  <nav>
    <span class="abs nav active" style="left:358px">Home</span>
    <span class="abs nav" style="left:411px">About Us</span>
    <span class="abs nav" style="left:466px">Product</span>
    <span class="abs nav" style="left:522px">Creation</span>
    <span class="abs nav" style="left:581px">Contact us</span>
  </nav>
  <div class="abs nav-bar"></div>
</header>

<section>
  <div class="abs hero" role="img" aria-label="Photo of a white paper vertical sundial with hour lines and a folded gnomon, lying on green grass"></div>
  <div class="abs hero-band"></div>
  <h1 class="abs hero-title">Paper Sundial</h1>
  <span class="abs dot on" style="left:567px"></span>
  <span class="abs dot" style="left:581px"></span>
  <span class="abs dot" style="left:594px"></span>
</section>

<section>
  <div class="abs welcome-art" role="img" aria-label="Drawing of the printable cut-out paper sundial template with hour lines and fold lines"></div>
  <h2 class="abs heading welcome-title">Welcome to Gnomonvale</h2>
  <div class="abs welcome-copy">
    <p>This page is about Sundials. Sundials are instruments that tell you the time with the shadow of the sun. To design a sundial you need to know exactly where you are going to put it, i.e. you need to know the longitude, the latitude and the orientation of the wall with respect to North.</p>
    <p>I have designed this page and integrated Orbila Maps. It helps you to easily find all the parameters needed and finally produces a printable page with a cut-out paper sundial, that can be cut and folded to give you a vertical sundial.<br>This page allows you to make your own Cut Out Paper Vertical Sundial customized to your place on earth and the declination of the wall you are going to put it on.</p>
  </div>
  <a class="abs btn btn-more">Read More</a>
</section>

<div class="abs rule" style="top:552px"></div>
<section>
  <div class="abs creation"></div>
  <h2 class="abs heading section-title" style="top:577px">Creation/edit sundial</h2>

  <div class="abs step" style="left:122px">
    <svg viewBox="0 0 22 24" fill="none" stroke="#333" stroke-width="1.3"><rect x="2" y="2" width="18" height="20" rx="1"/><line x1="2" y1="7" x2="20" y2="7"/><g fill="#333" stroke="none"><rect x="5" y="10" width="3" height="2.5"/><rect x="9.5" y="10" width="3" height="2.5"/><rect x="14" y="10" width="3" height="2.5"/><rect x="5" y="14" width="3" height="2.5"/><rect x="9.5" y="14" width="3" height="2.5"/><rect x="14" y="14" width="3" height="2.5"/><rect x="5" y="18" width="3" height="2.5"/><rect x="9.5" y="18" width="3" height="2.5"/><rect x="14" y="18" width="3" height="2.5"/></g></svg>
    <div class="step-name">CALCULATE</div>
    <div class="step-text">Fill in the form and create<br>your sundial</div>
  </div>
  <div class="abs step" style="left:230px">
    <svg viewBox="0 0 22 24" fill="none" stroke="#333" stroke-width="1.3"><path d="M4 2h10l5 5v15H4z"/><path d="M14 2v5h5"/><path d="M8 18c2-4 3-8 3-10s-1 0 0 3 4 5 5 6-6 0-8 1z" stroke-width=".9"/></svg>
    <div class="step-name">PRINT PDF</div>
    <div class="step-text">Fill in the form and create<br>your sundial</div>
  </div>
  <div class="abs step" style="left:337px">
    <svg viewBox="0 0 22 24" fill="none" stroke="#333" stroke-width="1.3"><circle cx="5" cy="8" r="3"/><circle cx="5" cy="17" r="3"/><path d="M7.5 9.5 20 17M7.5 15.5 20 7"/></svg>
    <div class="step-name">CUT AND FOLD</div>
    <div class="step-text">Fill in the form and create<br>your sundial</div>
  </div>
  <div class="abs step" style="left:454px">
    <svg viewBox="0 0 22 24" fill="none" stroke="#333" stroke-width="1.3"><rect x="4" y="2" width="14" height="20"/><g fill="#333" stroke="none"><rect x="7" y="5" width="2" height="2"/><rect x="10" y="5" width="2" height="2"/><rect x="13" y="5" width="2" height="2"/><rect x="7" y="9" width="2" height="2"/><rect x="10" y="9" width="2" height="2"/><rect x="13" y="9" width="2" height="2"/><rect x="7" y="13" width="2" height="2"/><rect x="10" y="13" width="2" height="2"/><rect x="13" y="13" width="2" height="2"/><rect x="9.5" y="17" width="3" height="5"/></g></svg>
    <div class="step-name">PUT WALL</div>
    <div class="step-text">Fill in the form and create<br>your sundial</div>
  </div>
  <div class="abs step" style="left:557px">
    <svg viewBox="0 0 22 24" fill="none" stroke="#333" stroke-width="1.3"><rect x="3" y="11" width="4" height="10"/><path d="M7 12l4-5c1-2 1-5 2-5 2 0 2 3 1 6h5c1 0 2 1 1.5 2.5L19 20c-.3 1-1 1-2 1H7"/></svg>
    <div class="step-name">ENJOY</div>
    <div class="step-text">Fill in the form and create<br>your sundial</div>
  </div>
</section>

<div class="abs rule" style="top:752px"></div>
<section>
  <h2 class="abs heading section-title" style="top:773px">View created sundial</h2>
  <div class="abs arrows">‹ ›</div>

  <article class="abs card" style="left:74px">
    <div class="card-photo" role="img" aria-label="Photo of a white paper sundial fixed on a brick wall" style="background:linear-gradient(90deg,#5a7088,#d8dce4 50%,#9a5a40)"></div>
    <h3 class="card-title">Foto enviada</h3>
    <p class="card-text">Reloj de pizarra y laton/sundial made<br>with slate and brass</p>
    <a class="btn btn-buy">Buy sundial</a>
  </article>
  <article class="abs card" style="left:209px">
    <div class="card-photo" role="img" aria-label="Photo of a dark slate sundial with a brass gnomon" style="background:linear-gradient(160deg,#8a8480,#4a3c36 45%,#3a2e2a)"></div>
    <h3 class="card-title">Foto enviada</h3>
    <p class="card-text">Reloj de pizarra y laton/sundial made<br>with slate and brass</p>
    <a class="btn btn-buy">Buy sundial</a>
  </article>
  <article class="abs card" style="left:344px">
    <div class="card-photo" role="img" aria-label="Photo of a wooden sundial with hour numbers and a dark gnomon" style="background:linear-gradient(160deg,#e8e4de,#d8a060 40%,#c88a48)"></div>
    <h3 class="card-title">Foto enviada</h3>
    <p class="card-text">Reloj de pizarra y laton/sundial made<br>with slate and brass</p>
    <a class="btn btn-buy">Buy sundial</a>
  </article>
  <article class="abs card" style="left:479px">
    <div class="card-photo" role="img" aria-label="Photo of a grey vertical sundial mounted outdoors" style="background:linear-gradient(90deg,#6a7a70,#a8b0b4 40%,#c0c6ca 70%,#6a7a70)"></div>
    <h3 class="card-title">Foto enviada</h3>
    <p class="card-text">Reloj de pizarra y laton/sundial made<br>with slate and brass</p>
    <a class="btn btn-buy">Buy sundial</a>
  </article>
</section>

<footer>
  <div class="abs footer-rule"></div>
  <div class="abs footer"></div>

  <h4 class="abs f-title" style="left:74px">Quick Links</h4>
  <ul class="abs f-links">
    <li>Home</li><li>About Us</li><li>product</li><li>Creation</li><li>Contact us</li>
  </ul>

  <h4 class="abs f-title" style="left:185px">Contact us</h4>
  <ul class="abs f-contact">
    <li><svg viewBox="0 0 8 8"><path d="M1 3c0-1 1-2 3-2s3 1 3 2v1H5V3H3v1H1zM1.5 4.5h5V7h-5z"/></svg>(555) 014-2290</li>
    <li><svg viewBox="0 0 8 8"><path d="M2 1h4v2H2zM1 3h6v3H6V5H2v1H1zM2 5h4v2H2z"/></svg>(555) 014-7713</li>
    <li><svg viewBox="0 0 8 8"><path d="M0.5 1.5h7v5h-7zM1 2l3 2.2L7 2" fill="none" stroke="#ddd" stroke-width=".8"/></svg><u>hello@gnomonvale.com</u></li>
    <li><svg viewBox="0 0 8 8"><path d="M4 0.5a2.5 2.5 0 0 1 2.5 2.5C6.5 5 4 7.5 4 7.5S1.5 5 1.5 3A2.5 2.5 0 0 1 4 .5zm0 1.6a.9.9 0 1 0 0 1.8.9.9 0 0 0 0-1.8z"/></svg><span>#2868 Lorem ipsum dolor sit amet,<br>consectetur adipiscing elit</span></li>
  </ul>

  <h4 class="abs f-title" style="left:331px">Newsletter</h4>
  <p class="abs f-note">Sign Up for Our Newsletter &amp; Promotion</p>
  <div class="abs f-input">Enter Your email Id</div>
  <a class="abs btn f-btn">SUBSCRIBE</a>

  <div class="abs f-brand"><span class="brand-dot"></span>Gnomonvale.com</div>
  <span class="abs social" style="left:513px"></span>
  <span class="abs social" style="left:536px"></span>
  <span class="abs social" style="left:558px"></span>
  <span class="abs social" style="left:581px"></span>

  <div class="abs footer-bottom">© 2016 gnomonvale.com&nbsp; All Rights Reserved</div>
</footer>

</body>
</html>
```